q-zen design for startup inpection service

building and pest inspections what i had in mind was q-zen in large print with prepurchase in small print directly under it and the small tm (tradmark) .Within the C I would like an eye but I don't want to take away from the C so maybe the eye would be done in a fine line?I would also like the Building and Pest inspections to be prominent and large .Have no idea of colors but do like black orange and silver

Target Market(s)

home buyers and realestate agents

Industry/Entity Type

Building

Contact Information for Business Card

q-zen prepurchase, Phone 0412093816, fax 02 71934058, email q-zen@mailbrook.com.au ,building and pest inspections

Font styles to use
Sans Serif

Requirements
Must have
• bold color
• simple layout
• bold color
• uncluttered layout
Should not have
• contact details the same size as Building and Pest Inspections

```html
<!DOCTYPE html>
<html lang="en">
<head>
<meta charset="utf-8">
<title>q-zen prepurchase – Business Card</title>
<link rel="stylesheet" href="https://fonts.googleapis.com/css2?family=Fira+Sans+Condensed:wght@600&family=Fira+Sans:wght@400;500;700&display=swap">
<style>
  :root {
    --paper: #f2f4f4;
    --brand-blue: #0428c0;
    --brand-red: #e01a06;
    --band-grey: #e6e8e8;
    --ink: #3f4446;
    --ink-icon: #1f3560;
    --white: #ffffff;
  }
  * { margin: 0; padding: 0; box-sizing: border-box; }
  html, body { width: 741px; height: 1200px; overflow: hidden; background: var(--paper); }
  .card {
    position: relative;
    width: 741px;
    height: 1200px;
    background: var(--paper);
    overflow: hidden;
    font-family: "Fira Sans", sans-serif;
  }
  .side-bar-blue {
    position: absolute; left: 0; top: 0;
    width: 81px; height: 765px;
    background: var(--brand-blue);
  }
  .side-bar-red {
    position: absolute; left: 0; top: 1078px;
    width: 81px; height: 122px;
    background: var(--brand-red);
  }
  .title-band {
    position: absolute; left: 269px; top: 178px;
    width: 472px; height: 85px;
    background: var(--brand-blue);
  }
  .title-band h1 {
    position: absolute; right: 56px; top: 14px;
    font-family: "Fira Sans Condensed", sans-serif;
    font-weight: 600;
    font-size: 54px;
    line-height: 1;
    color: var(--white);
    letter-spacing: -0.5px;
    white-space: nowrap;
  }
  .tagline {
    position: absolute; right: 56px; top: 270px;
    font-size: 40px;
    font-weight: 500;
    line-height: 1.1;
    color: var(--ink);
    white-space: nowrap;
  }
  .brand {
    position: absolute; left: 130px; top: 560px;
    display: flex; align-items: center; gap: 22px;
  }
  .brand-dot {
    width: 150px; height: 150px;
    border-radius: 50%;
    background: var(--brand-blue);
  }
  .brand-name {
    font-family: "Fira Sans", sans-serif;
    font-weight: 700;
    font-size: 96px;
    line-height: 1;
    color: var(--brand-blue);
  }
  .contact-list { list-style: none; }
  .contact-row {
    position: absolute; left: 0;
    width: 649px; height: 72px;
    background: var(--band-grey);
    display: flex; align-items: center;
  }
  .contact-row.phone { top: 766px; }
  .contact-row.fax { top: 884px; }
  .contact-row.email { top: 1003px; }
  .contact-icon {
    width: 26px; height: 26px;
    margin-left: 97px; margin-right: 35px;
    flex: none;
  }
  .contact-text {
    font-size: 30px;
    color: var(--ink);
    letter-spacing: 0.5px;
    white-space: nowrap;
  }
</style>
</head>
<body>
<div class="card">
  <div class="side-bar-blue"></div>
  <div class="side-bar-red"></div>

  <div class="title-band"><h1>q-zen prepurchase</h1></div>
  <p class="tagline">Building and Pest inspections</p>

  <div class="brand">
    <div class="brand-dot"></div>
    <span class="brand-name">q-zen</span>
  </div>

  <ul class="contact-list">
    <li class="contact-row phone">
      <svg class="contact-icon" viewBox="0 0 26 26" aria-hidden="true">
        <path d="M10 4 h4 v5 h-3 q-1 4 0 8 h3 v5 h-4 q-5 -9 0 -18z" fill="var(--ink-icon)"/>
      </svg>
      <span class="contact-text">0412093816</span>
    </li>
    <li class="contact-row fax">
      <svg class="contact-icon" viewBox="0 0 26 26" aria-hidden="true" fill="none" stroke="var(--ink-icon)" stroke-width="2">
        <rect x="7" y="2" width="12" height="9"/>
        <rect x="2" y="11" width="22" height="8"/>
        <rect x="2" y="20" width="22" height="4"/>
        <line x1="5" y1="15" x2="10" y2="15"/>
      </svg>
      <span class="contact-text">02 71934058</span>
    </li>
    <li class="contact-row email">
      <svg class="contact-icon" viewBox="0 0 26 26" aria-hidden="true" fill="none" stroke="var(--ink-icon)" stroke-width="2">
        <rect x="2" y="6" width="22" height="15"/>
        <polyline points="2,6 13,15 24,6"/>
        <line x1="2" y1="21" x2="10" y2="13"/>
        <line x1="24" y1="21" x2="16" y2="13"/>
      </svg>
      <span class="contact-text">q-zen@mailbrook.com.au</span>
    </li>
  </ul>
</div>
</body>
</html>
```